Calm Compass website development

Need a website designed for a coaching business. Very high-end, luxury, professionalism, in the area of STRESS, see brief attached. I have a logo already
Updates

Slow in providing feedback

Target Market(s)

CEOs very successful men and wealthy females, high end luxury market

Industry/Entity Type

coaching

Number of Pages Required

1 page

Requirements
Must have
• Luxury look, professional, serious but warm, appealing to both sexes

```html
<!DOCTYPE html>
<html lang="en">
<head>
<meta charset="utf-8">
<title>Calm Compass – Lifestyle Coaching</title>
<link href="https://fonts.googleapis.com/css2?family=Roboto+Condensed:wght@300;400;700&display=swap" rel="stylesheet">
<style>
:root{
  --ink:#1d1b1c;
  --ink-soft:#2a282a;
  --slate:#707074;
  --band:#77777f;
  --paper:#ffffff;
  --mist:#dcdad5;
  --body:#666669;
  --tab:#56565a;
}
*{margin:0;padding:0;box-sizing:border-box}
html,body{width:1200px;height:3053px;overflow:hidden;background:var(--paper)}
body{position:relative;font-family:'Roboto Condensed',Arial,sans-serif;color:var(--ink)}
.abs{position:absolute}
.shapes{position:absolute;left:0;top:0}
.call{left:742px;top:10px;color:#fff;font-size:23px;font-weight:400;letter-spacing:.2px;display:flex;align-items:center;gap:10px}
.call svg{width:34px;height:34px}
.brand{left:140px;top:92px;width:210px;text-align:center}
.brand-name{font-size:25px;font-weight:700;letter-spacing:4px;color:var(--ink)}
.brand-tag{font-size:9px;letter-spacing:2px;color:var(--ink)}
.nav{left:516px;top:84px;display:flex;gap:33px;font-size:18px;font-weight:400;color:var(--ink)}
.nav .on{color:#8a8a8e}
.hero-title{left:138px;top:300px;font-size:112px;font-weight:700;letter-spacing:-1px;line-height:1}
.btn{height:76px;width:214px;border-radius:38px;color:#fff;font-size:22px;font-weight:400;display:flex;align-items:center;justify-content:center}
.btn-dark{background:var(--ink)}
.btn-slate{background:var(--slate)}
.dots{left:1105px;top:396px}
.dots span{display:block;width:9px;height:9px;border-radius:50%;background:#fff;margin-bottom:8px}
.dots span.on{background:#8a8a8e}
.welcome-title{left:144px;top:784px;font-size:52px;font-weight:700;line-height:56px}
.rule{height:3px;background:var(--ink)}
.welcome-text{left:144px;top:922px;width:912px;font-size:17.5px;font-weight:300;color:var(--body);line-height:30.5px}
.welcome-text p{margin-bottom:0}
.why-title{left:144px;top:1478px;font-size:50px;font-weight:700;color:#fff}
.why-list{left:144px;top:1568px;width:540px;list-style:none;color:#fff;font-size:19px;font-weight:300;line-height:36px}
.why-list li{position:relative;padding-left:38px}
.why-list svg{position:absolute;left:0;top:10px;width:22px;height:18px}
.benefits-title{left:0;top:2016px;width:1200px;text-align:center;font-size:52px;font-weight:700;color:var(--ink)}
.hex-text{width:214px;text-align:center;color:#fff;font-size:14.5px;font-weight:400;line-height:21.5px}
.hex-num{display:block;font-size:26px;font-weight:700;margin-bottom:12px}
.exp{width:214px;text-align:center;color:#fff;font-weight:700}
.foot-brand{left:143px;top:2870px;width:250px;text-align:center;color:#fff}
.foot-brand .brand-name{color:#fff;font-size:34px;letter-spacing:5px;font-weight:400}
.foot-brand .brand-tag{color:#fff;font-size:14px;letter-spacing:4px;margin-top:2px}
.foot-nav{left:493px;top:2850px;display:flex;gap:33px;color:#fff;font-size:18px}
.legal{left:493px;top:2909px;color:#fff;font-size:15px;font-weight:300}
.social{left:492px;top:2963px;display:flex;gap:10px}
.social span{width:42px;height:42px;border-radius:50%;border:2px solid #fff;display:block}
</style>
</head>
<body>

<svg class="shapes" width="1200" height="3053" viewBox="0 0 1200 3053" aria-hidden="false">
  <defs>
    <linearGradient id="heroPhoto" x1="0" y1="0" x2="1" y2="0">
      <stop offset="0" stop-color="#dedcd7"/>
      <stop offset=".55" stop-color="#d8d4cc"/>
      <stop offset=".8" stop-color="#b98a68"/>
      <stop offset="1" stop-color="#c9b8a6"/>
    </linearGradient>
    <linearGradient id="hexPhoto" x1="0" y1="0" x2="1" y2="1">
      <stop offset="0" stop-color="#a7886a"/>
      <stop offset=".5" stop-color="#7a5a45"/>
      <stop offset="1" stop-color="#4e4a48"/>
    </linearGradient>
    <linearGradient id="benefitPhoto" x1="0" y1="0" x2="1" y2="0">
      <stop offset="0" stop-color="#9a9a9a"/>
      <stop offset=".45" stop-color="#d4d4d4"/>
      <stop offset="1" stop-color="#5e5e5e"/>
    </linearGradient>
  </defs>

  <!-- header -->
  <rect x="0" y="0" width="1200" height="3" fill="#555"/>
  <polygon points="680,3 1050,3 1020,52 710,52" fill="var(--tab)"/>

  <!-- hero -->
  <rect x="0" y="130" width="1200" height="564" fill="url(#heroPhoto)" role="img" aria-label="Smiling woman resting her chin on her hand, holding a mug"/>
  <polygon points="820,694 1015,582 1200,690 1200,694" fill="#fff"/>
  <circle cx="245" cy="88" r="105" fill="#fff"/>
  <circle cx="245" cy="52" r="26" fill="var(--ink)"/>

  <!-- welcome rules -->
  <rect x="52" y="812" width="78" height="3" fill="var(--ink)"/>
  <rect x="452" y="867" width="78" height="3" fill="var(--ink)"/>

  <!-- why me band -->
  <polygon points="0,1383 720,1383 978,1235 1200,1362 1200,1913 0,1913" fill="var(--band)" role="img" aria-label="Faded photo of people in a coaching session"/>
  <polygon points="976,1283 1180,1400 1180,1645 976,1763 772,1645 772,1400" fill="url(#hexPhoto)" role="img" aria-label="Laughing woman holding a cup in warm sunlight"/>

  <!-- benefits -->
  <rect x="0" y="1913" width="1200" height="855" fill="url(#benefitPhoto)" role="img" aria-label="Black and white photo of a coach talking with a client"/>
  <rect x="412" y="2047" width="80" height="3" fill="var(--ink)"/>
  <rect x="708" y="2047" width="80" height="3" fill="var(--ink)"/>

  <polygon points="336,2123 464,2197 464,2345 336,2419 208,2345 208,2197" fill="var(--ink-soft)"/>
  <polygon points="600,2123 728,2197 728,2345 600,2419 472,2345 472,2197" fill="var(--slate)"/>
  <polygon points="864,2123 992,2197 992,2345 864,2419 736,2345 736,2197" fill="var(--ink)"/>
  <polygon points="468,2354 596,2428 596,2576 468,2650 340,2576 340,2428" fill="var(--ink)"/>
  <polygon points="732,2354 860,2428 860,2576 732,2650 604,2576 604,2428" fill="var(--slate)"/>

  <!-- people icon -->
  <g fill="#fff">
    <circle cx="338" cy="2214" r="24"/>
    <circle cx="288" cy="2222" r="16"/>
    <circle cx="388" cy="2222" r="16"/>
    <path d="M298 2295 q0-50 40-50 q40 0 40 50 z"/>
    <path d="M262 2282 q0-36 28-36 q18 0 22 12 q-14 12-14 24 z"/>
    <path d="M414 2282 q0-36 -28-36 q-18 0 -22 12 q14 12 14 24 z"/>
  </g>

  <!-- footer -->
  <polygon points="0,2768 0,2760 205,2645 425,2768" fill="var(--ink)"/>
  <rect x="0" y="2768" width="1200" height="285" fill="var(--ink)"/>
  <circle cx="270" cy="2795" r="42" fill="#fff"/>
</svg>

<div class="abs call">
  <svg viewBox="0 0 34 34"><circle cx="17" cy="17" r="15" fill="none" stroke="#fff" stroke-width="2"/><path d="M12 9l3 0 1.5 4-2 1.5c1 2.2 2.8 4 5 5l1.5-2 4 1.5v3c0 1-1 2-2 2C15 24 10 19 10 11c0-1 1-2 2-2z" fill="#fff"/></svg>
  CALL : +1 555 014 2280
</div>

<div class="abs brand">
  <div class="brand-name">CALM COMPASS</div>
  <div class="brand-tag">— LIFESTYLE COACHING —</div>
</div>

<nav class="abs nav">
  <span class="on">HOME</span><span>ABOUT</span><span>SERVICES</span><span>WHY ME?</span><span>BENEFITS</span><span>CONTACT</span>
</nav>

<h1 class="abs hero-title">HEAD COACH</h1>
<div class="abs btn btn-dark" style="left:144px;top:460px">MEN</div>
<div class="abs btn btn-slate" style="left:369px;top:460px">WOMEN</div>
<div class="abs dots"><span></span><span class="on"></span><span></span><span></span></div>

<h2 class="abs welcome-title">WELCOME TO<br>CALMCOMPASS</h2>
<div class="abs welcome-text">
  <p>Calm Compass came about due to my desire to help people lead a better and healthier life. Initially, I was involved in the fitness/body side of health. As years passed and my experience grew, I realized how important the mind was in total wellness, and that the mind is all powerful and controlling. Control the mind, control the body and achieve success. Stress can be the most debilating factor in our lives, it is the root cause of so many diseases and costs the US workplace an estimated 300 billion dollars due to loss of productivity .</p>
  <p>However stress is not all bad...we need stress to survive and peform at an optional level. In order to do that, you need to recognize your stressors and then control them, and put it to good use when neccsary.Stress is not all bad, and since we are surrounded by engulfed by stress, or it isn't going anywhere soon,we need to deal with it, and even better, channel to be an advantage/tool to perform better.</p>
</div>
<div class="abs btn btn-dark" style="left:144px;top:1205px">READ MORE</div>

<h2 class="abs why-title">WHY ME?</h2>
<ul class="abs why-list">
  <li><svg viewBox="0 0 22 18"><path d="M2 9l6 6L20 3" fill="none" stroke="#fff" stroke-width="3.5"/></svg>Been there done that! Have been through a lot, started businesses, selling a business, law suits,marriage, divorce, second marriage, kids, school, sports, fights, robbed, gun in face, traveled the world, successful, two great kids (both Cadets at Ridgeview Academy...duty/ honor/country)</li>
  <li><svg viewBox="0 0 22 18"><path d="M2 9l6 6L20 3" fill="none" stroke="#fff" stroke-width="3.5"/></svg>Limited number of clients...different stage of life, empty nester, have a full career...won't be a number</li>
</ul>

<h2 class="abs benefits-title">BENEFITS</h2>

<div class="abs exp" style="left:229px;top:2312px;font-size:28px">EXPERIENCE</div>
<div class="abs exp" style="left:229px;top:2358px;font-size:26px">01</div>

<div class="abs hex-text" style="left:493px;top:2180px"><span class="hex-num">02</span>Sector expert Health/Wellness. Presented at numerous industry shows and quoted in national publications (not as a coach, I'm new, but in the health &amp; wellness space)</div>
<div class="abs hex-text" style="left:757px;top:2180px"><span class="hex-num">03</span>Excellent listener...being in sales for many years, the secret is to really listen...and get to the end game, and make it feel as if it was their decision. Not sure how to word this as a benefit.</div>
<div class="abs hex-text" style="left:353px;top:2368px"><span class="hex-num">04</span>Access/resources industry professionals, sport psychologist just spent a few hours with the Mind performance coach for the Harbor City Hawks baseball team...I can get the best advice and latest techniques in mind/body training performance.</div>
<div class="abs hex-text" style="left:625px;top:2386px"><span class="hex-num">05</span>Private, more than happy to sign confidentiality agreement. Especially for the business man.</div>

<div class="abs foot-brand">
  <div class="brand-name">CALM COMPASS</div>
  <div class="brand-tag">— LIFESTYLE COACHING —</div>
</div>
<nav class="abs foot-nav"><span>HOME</span><span>ABOUT</span><span>SERVICES</span><span>WHY ME?</span><span>BENEFITS</span><span>CONTACT</span></nav>
<div class="abs legal">© 2022 Calm Compass.All rights reserved &nbsp;|&nbsp; Privacy &nbsp;|&nbsp; Terms of Use</div>
<div class="abs social" aria-label="Social links"><span></span><span></span><span></span><span></span></div>

</body>
</html>
```